Counseling Practice Business Card

I need a professional looking business card incorporating my new logo that was just completed. Card needs to incorporate my name and title, description of my specialty, my address, my phone number, my fax number, my email and my website URL. I need to be able to choose design on/with different paper colors and textures.
I do not have a lot of business card ideas so I am open to anything but I want bold,sharp, clear card without additional designs other than my logo (see attached file info). I am open to different color backgrounds or paper colors including black. I do not like traditional brackets around area codes in phone number or dashes between numbers in phone number. Am open to other ways of presenting including periods between numbers as appropriate. I do not know enough to know what I like yet but I want card to coordinate and work together with my logo. My practice emphasizes natural mental health interventions so any use of color (with background paper color or the blue and green in my logo) that elicits nature is nice. In addition to black, any natural brown or wood looking background might be desirable also. Most of the offerings so far look very similar and boring.

Target Market(s)

Potential therapy clients and other professionals

Contact Information for Business Card

Card information:
Gerald M. Whitcombe, Ph.D.
Licensed Clinical Psychologist
Integrative Health Coach
4812 Marlowe Ridge Blvd SE
Suite 310
Duluth, GA 30096
(770) 415-2983 phone
(770) 581-4096 fax
drgeraldwhitcombe@quillmarsh.net
brightfernwellness.net

Font styles to use
Serif
Sans Serif
Other font styles liked:
• anything that you think looks crisp, clear and easily readable

Requirements
Must have
• Any color used should coordinate with my logo design (see attached files).
• Card should be printed horizontally so top and bottom are longest sides of rectangle.
• Background color or paper color should complement and highlight logo. Do not like a white background. black, grey, brown or any color my logo would blend well with.
Nice to have
• I would like designer to utilize color to highlight letters/name or phone-fax-web symbols.
• Bottom edge of card could be highlighted if appropriate to an idea.
Should not have
• I would NOT want the card to have a pure white background at all.
• No clear cards.
• Cards should be oriented with long sides on bottom and top, NOT sides. DO NOT LIKE THIS THIN TALL ORIENTATION.

```html
<!DOCTYPE html>
<html lang="en">
<head>
<meta charset="utf-8">
<title>Brightfern Wellness – Business Card</title>
<link href="https://fonts.googleapis.com/css2?family=Roboto:wght@400;500&family=Roboto+Condensed:wght@700&display=swap" rel="stylesheet">
<style>
  :root {
    --backdrop: #2f2f31;
    --kraft: #cdae80;
    --kraft-deep: #b8976a;
    --teal: #2c6a7d;
    --green: #1d6a2e;
    --ink: #1c1a17;
  }
  html, body {
    margin: 0;
    padding: 0;
    width: 799px;
    height: 1200px;
    overflow: hidden;
    background: var(--backdrop);
  }
  .stage {
    position: relative;
    width: 799px;
    height: 1200px;
  }
  .card {
    position: absolute;
    left: 80px;
    width: 640px;
    height: 366px;
    background: var(--kraft);
    overflow: hidden;
    box-shadow: 0 6px 18px rgba(0,0,0,.45);
  }
  .card--front { top: 120px; }
  .card--back  { top: 710px; }

  .front-name {
    position: absolute;
    left: 0; right: 0;
    top: 140px;
    text-align: center;
    font-family: "Roboto Condensed", sans-serif;
    font-weight: 700;
    font-size: 52px;
    letter-spacing: 1px;
    color: var(--kraft-deep);
  }

  .back-name {
    position: absolute;
    left: 30px;
    top: 34px;
    font-family: "Roboto Condensed", sans-serif;
    font-weight: 700;
    font-size: 36px;
    color: var(--teal);
  }
  .person {
    position: absolute;
    left: 30px;
    top: 112px;
    font-family: "Roboto", sans-serif;
    color: var(--ink);
  }
  .person__name {
    font-family: "Roboto Condensed", sans-serif;
    font-weight: 700;
    font-size: 20px;
    color: var(--teal);
    margin: 0 0 4px;
  }
  .person__title {
    font-size: 13px;
    line-height: 17px;
    margin: 0;
  }
  .address {
    position: absolute;
    right: 30px;
    top: 128px;
    text-align: right;
    font-family: "Roboto", sans-serif;
    font-weight: 500;
    font-size: 14px;
    line-height: 19px;
    color: var(--ink);
    margin: 0;
  }
  .wave {
    position: absolute;
    left: 0; top: 0;
    width: 640px;
    height: 366px;
  }
  .contact {
    position: absolute;
    right: 24px;
    top: 262px;
    margin: 0;
    padding: 0;
    list-style: none;
    font-family: "Roboto", sans-serif;
    font-size: 15px;
    line-height: 22px;
    color: var(--kraft);
    text-align: right;
  }
  .contact li {
    display: flex;
    justify-content: flex-end;
    align-items: center;
    gap: 10px;
  }
  .contact svg {
    width: 14px;
    height: 14px;
    fill: var(--kraft);
    flex: none;
  }
</style>
</head>
<body>
<div class="stage">

  <section class="card card--front">
    <div class="front-name">Brightfern Wellness</div>
  </section>

  <section class="card card--back">
    <svg class="wave" viewBox="0 0 640 366" aria-hidden="true">
      <path d="M0,212 C120,300 300,272 430,258 C530,248 600,252 640,268 L640,366 L0,366 Z" fill="var(--teal)"/>
      <path d="M0,188 C110,250 280,250 420,238 C520,230 600,238 640,262 L640,270 C600,248 520,242 420,250 C280,262 110,264 0,200 Z" fill="var(--green)"/>
      <path d="M20,214 C120,262 240,270 330,266" fill="none" stroke="var(--green)" stroke-width="3"/>
    </svg>

    <div class="back-name">Brightfern Wellness</div>

    <div class="person">
      <p class="person__name">Gerald M. Whitcombe, Ph.D.</p>
      <p class="person__title">Licensed Clinical Psychologist</p>
      <p class="person__title">Integrative Health Coach</p>
    </div>

    <p class="address">4812 Marlowe Ridge Blvd SE<br>Suite 310 Duluth, GA 30096</p>

    <ul class="contact">
      <li>770.415.2983
        <svg viewBox="0 0 16 16"><path d="M2 5c0-2 2-3 6-3s6 1 6 3v1h-3V5H5v1H2z M4 7h8l2 6H2z"/></svg></li>
      <li>770.581.4096
        <svg viewBox="0 0 16 16"><path d="M4 1h8v4H4z M1 6h14v6h-3v3H4v-3H1z M5 10v4h6v-4z"/></svg></li>
      <li>www.brightfernwellness.net
        <svg viewBox="0 0 16 16"><path d="M8 1a7 7 0 1 0 0 14A7 7 0 0 0 8 1zm0 1.5c.9 0 1.8 2 2 4.5H6c.2-2.5 1.1-4.5 2-4.5zM2.6 7h2A11 11 0 0 1 5.3 3 5.5 5.5 0 0 0 2.6 7zm8.8 0h2a5.5 5.5 0 0 0-2.7-4A11 11 0 0 1 11.4 7zM2.6 9a5.5 5.5 0 0 0 2.7 4A11 11 0 0 1 4.6 9zm3.4 0c.2 2.5 1.1 4.5 2 4.5s1.8-2 2-4.5zm5.4 0a11 11 0 0 1-.7 4 5.5 5.5 0 0 0 2.7-4z"/></svg></li>
      <li>drgeraldwhitcombe@quillmarsh.net
        <svg viewBox="0 0 16 16"><path d="M1 3h14v10H1z M2 4l6 5 6-5" stroke="var(--teal)" stroke-width="1.2"/></svg></li>
    </ul>
  </section>

</div>
</body>
</html>
```